The Plate Compass

Cutting Through the Noise to What Actually Works.

Nutrition book

Target Market(s)

People looking to be or get healthy and eat right.

```html
<!DOCTYPE html>
<html lang="en">
<head>
<meta charset="utf-8">
<title>The Plate Compass – Book Cover</title>
<link rel="stylesheet" href="https://fonts.googleapis.com/css2?family=Montserrat:wght@800;900&family=Oswald:wght@500&family=Caveat:wght@500&family=Raleway:wght@500&display=swap">
<style>
  :root {
    --page-bg: #efe9e2;
    --cover-orange: #d25a2b;
    --cover-orange-deep: #c44f22;
    --title-white: #ffffff;
    --accent-green: #a8ee5c;
    --subtitle-pink: #f5c9d9;
    --author-tint: #f6dccf;
    --art-start: #d8d6d2;
    --art-end: #9cae7c;
  }
  * { box-sizing: border-box; margin: 0; padding: 0; }
  html, body {
    width: 1200px; height: 1200px; overflow: hidden;
    background: var(--page-bg);
  }
  .canvas {
    width: 1200px; height: 1200px;
    display: flex; align-items: center; justify-content: center;
  }
  .book-cover {
    position: relative;
    width: 760px; height: 1140px;
    background: linear-gradient(160deg, var(--cover-orange) 0%, var(--cover-orange-deep) 100%);
    box-shadow: 0 18px 40px rgba(0,0,0,0.18);
    overflow: hidden;
  }
  .title {
    position: absolute; left: 0; right: 0; top: 70px;
    text-align: center;
    font-family: 'Montserrat', sans-serif;
    line-height: 0.95;
  }
  .title-lead {
    display: block;
    font-weight: 900; font-size: 108px;
    color: var(--title-white);
    letter-spacing: -3px;
  }
  .title-key {
    display: inline-block;
    font-weight: 900; font-size: 124px;
    color: var(--accent-green);
    letter-spacing: -3px;
    margin-top: 4px;
  }
  .title-underline {
    display: block; margin: 6px auto 0;
  }
  .subtitle {
    position: absolute; left: 60px; right: 60px; top: 400px;
    text-align: center;
    font-family: 'Oswald', sans-serif;
    font-weight: 500; font-size: 42px; line-height: 1.1;
    color: var(--subtitle-pink);
    text-transform: uppercase;
  }
  .cover-artwork {
    position: absolute; left: 70px; top: 550px;
    width: 500px; height: 390px;
    border-radius: 24px;
    background: linear-gradient(90deg, var(--art-start) 0%, var(--art-end) 100%);
  }
  .tagline {
    position: absolute; left: 584px; top: 740px;
    width: 160px;
    font-family: 'Caveat', cursive;
    font-weight: 500; font-size: 34px; line-height: 1.08;
    color: var(--accent-green);
    text-align: center;
  }
  .tagline-rule {
    display: block; width: 44px; height: 3px;
    background: var(--accent-green);
    margin: 8px auto 0;
  }
  .author {
    position: absolute; left: 0; width: 580px; top: 1010px;
    text-align: center;
    font-family: 'Raleway', sans-serif;
    font-weight: 500; font-size: 24px;
    letter-spacing: 12px;
    color: var(--author-tint);
  }
</style>
</head>
<body>
<main class="canvas">
  <article class="book-cover">
    <h1 class="title">
      <span class="title-lead">The Plate</span>
      <span class="title-key">Compass</span>
      <svg class="title-underline" width="560" height="24" viewBox="0 0 560 24" aria-hidden="true">
        <path d="M4 8 L520 14 L556 22 L514 18 L4 14 Z" fill="var(--accent-green)"/>
      </svg>
    </h1>
    <p class="subtitle">Cutting through the noise to<br>what actually works.</p>
    <div class="cover-artwork" role="img" aria-label="Photo of a glass bowl split in two: crumpled paper balls labelled with diet fads on the left, salmon, avocado, greens, tomatoes, berries, nuts and quinoa on the right"></div>
    <p class="tagline">Less<br>Confusion<br>Better<br>Choices<br>A Healthier<br>You<span class="tagline-rule"></span></p>
    <p class="author">YOUR NAME HERE</p>
  </article>
</main>
</body>
</html>
```